Automotive Accessories Business Card

Design a business template that match our new logo design and our industry.

https://www.qelmotorgear.com/

Target Market(s)

Aftermarket auto parts and accessories

Industry/Entity Type

automotive

Contact Information for Business Card

company logo

Font styles to use
Serif
Sans Serif

Colors
EB3D1F
EC4F4E
F09395
F8D3D4
FCEDEE

```html
<!DOCTYPE html>
<html lang="en">
<head>
<meta charset="utf-8">
<title>QEL Motor Gear – Business Card</title>
<link href="https://fonts.googleapis.com/css2?family=Poppins:wght@400;500;600;700&display=swap" rel="stylesheet">
<style>
  :root {
    --brand-red: #d62530;
    --ink: #2f2f33;
    --text: #1e1e1e;
    --paper: #f7f7f7;
    --backdrop: #e4e4e4;
    --divider: #9a9a9a;
  }
  * { margin: 0; padding: 0; box-sizing: border-box; }
  html, body {
    width: 1200px; height: 930px; overflow: hidden;
    background: var(--backdrop);
    font-family: "Poppins", sans-serif;
  }
  .sheet {
    width: 1200px; height: 930px;
    display: flex; align-items: center; justify-content: center; gap: 44px;
  }
  .card {
    width: 525px; height: 300px;
    box-shadow: 0 10px 28px rgba(0,0,0,.14);
    position: relative;
    overflow: hidden;
  }
  .card--front { background: var(--paper); padding: 40px 36px 0; }
  .card--back {
    background: var(--brand-red);
    display: flex; align-items: center; justify-content: center;
  }
  .brand {
    display: flex; align-items: center; justify-content: center; gap: 12px;
    font-weight: 700; letter-spacing: 1px; line-height: 1; white-space: nowrap;
  }
  .brand__mark { width: 18px; height: 18px; flex: none; }
  .card--front .brand { color: var(--ink); font-size: 34px; }
  .card--front .brand__mark { background: var(--brand-red); }
  .card--back .brand { color: #fff; font-size: 44px; }
  .card--back .brand__mark { background: #fff; width: 22px; height: 22px; }
  .holder { text-align: center; margin-top: 26px; }
  .holder__name {
    color: var(--brand-red); font-weight: 500; font-size: 22px;
    letter-spacing: 1.5px; text-transform: uppercase;
  }
  .holder__role {
    color: var(--text); font-size: 11px; letter-spacing: 1.2px;
    text-transform: uppercase; margin-top: 2px;
  }
  .details {
    display: flex; justify-content: center; margin-top: 24px;
    font-size: 13px; color: var(--text); line-height: 1.55;
  }
  .details__address { text-align: right; padding-right: 16px; font-style: normal; white-space: nowrap; }
  .details__rule { width: 1px; background: var(--divider); }
  .details__contacts { padding-left: 16px; list-style: none; white-space: nowrap; }
  .details__contacts li { display: flex; align-items: center; gap: 8px; }
  .details__contacts svg { width: 12px; height: 12px; fill: var(--brand-red); flex: none; }
</style>
</head>
<body>
<main class="sheet">
  <section class="card card--front">
    <div class="brand"><span class="brand__mark"></span><span>QEL MOTOR GEAR</span></div>
    <div class="holder">
      <p class="holder__name">Daniel Marsh</p>
      <p class="holder__role">Managing Director</p>
    </div>
    <div class="details">
      <address class="details__address">
        87, Harbor Lane<br>Suite 12<br>30918, Eastvale
      </address>
      <span class="details__rule"></span>
      <ul class="details__contacts">
        <li>
          <svg viewBox="0 0 24 24" aria-hidden="true"><path d="M6.6 10.8a15.1 15.1 0 0 0 6.6 6.6l2.2-2.2a1 1 0 0 1 1-.25 11.4 11.4 0 0 0 3.6.57 1 1 0 0 1 1 1V20a1 1 0 0 1-1 1A17 17 0 0 1 3 4a1 1 0 0 1 1-1h3.5a1 1 0 0 1 1 1c0 1.25.2 2.45.57 3.57a1 1 0 0 1-.25 1z"/></svg>
          055-218 734 906
        </li>
        <li>
          <svg viewBox="0 0 24 24" aria-hidden="true"><path d="M2 5h20v14H2z"/><path d="M3 6l9 7 9-7" stroke="#fff" stroke-width="1.6" fill="none"/></svg>
          info@qelmotorgear.com
        </li>
        <li>
          <svg viewBox="0 0 24 24" aria-hidden="true"><circle cx="12" cy="12" r="10"/><path d="M2 12h20M12 2c3 3 3 17 0 20M12 2c-3 3-3 17 0 20" stroke="#fff" stroke-width="1.4" fill="none"/></svg>
          www.qelmotorgear.com
        </li>
      </ul>
    </div>
  </section>
  <section class="card card--back">
    <div class="brand"><span class="brand__mark"></span><span>QEL MOTOR GEAR</span></div>
  </section>
</main>
</body>
</html>
```